Business card design Needed for new logo / Construction business, home extensions and new builds

We need a business card design using our new logo files which i will attach to this project :)

We are a small construction business specialising in home extensions, new builds and property development. We are very ambitious and would appreciate professional and elegant designs for our new business card.

Very serious about using the services on MakerQuarry and recently acquired our new logo from here :)

Please get involved, i will feedback when i can as i am very busy but can respond daily, thanks

Target Market(s)

People that want to build onto their houses, new building developments or adding too their existing property

Industry/Entity Type

Construction

Contact Information for Business Card

Renwick Tolliver Construction, Lionel Ashby (Managing Director), Tel 07822254961, email - info@renwick-tolliver, www.renwick-tolliver.co.uk

Colors

Designer to choose colors to be used in the design.

Requirements
Must have
• I like a deep grey on the back please. A lot of you have provided black from and back, try mixing things up a little. The black looks cool 😎 Thanks

```html
<!DOCTYPE html>
<html lang="en">
<head>
<meta charset="utf-8">
<title>Renwick Tolliver Construction – Business Card</title>
<link href="https://fonts.googleapis.com/css2?family=Lato:wght@400;700;900&display=swap" rel="stylesheet">
<style>
  :root {
    --stage: #2a2a2b;
    --card-front: #1b1b1c;
    --card-back: #3a3a3d;
    --card-back-edge: #444447;
    --gold: #d9a528;
    --gold-line: #b8891f;
    --silver: #dcdcdc;
  }
  * { margin: 0; padding: 0; box-sizing: border-box; }
  html, body {
    width: 1200px; height: 875px; overflow: hidden;
    background: var(--stage);
    font-family: "Lato", sans-serif;
  }
  .stage {
    width: 1200px; height: 875px;
    display: flex; align-items: center; justify-content: center; gap: 48px;
  }
  .card {
    width: 540px; height: 309px;
    border-radius: 16px;
    position: relative;
    box-shadow: 0 20px 40px rgba(0,0,0,.45);
    overflow: hidden;
  }
  /* Front */
  .card-front {
    background: var(--card-front);
    display: flex; align-items: center; justify-content: center;
  }
  .brand { display: flex; flex-direction: column; align-items: center; gap: 18px; }
  .brand-mark { width: 34px; height: 34px; background: var(--gold); }
  .brand-name {
    font-weight: 700; font-size: 30px; letter-spacing: 3px;
    color: var(--gold); text-transform: uppercase; text-align: center; line-height: 1.25;
  }
  /* Back */
  .card-back { background: var(--card-back); border: 10px solid var(--card-back-edge); }
  .back-brand {
    position: absolute; top: 22px; right: 26px;
    font-weight: 700; font-size: 11px; letter-spacing: 1.5px;
    color: var(--gold); text-transform: uppercase;
    display: flex; align-items: center; gap: 8px;
  }
  .back-brand .brand-mark { width: 12px; height: 12px; }
  .holder { position: absolute; left: 30px; top: 112px; text-align: right; width: 225px; }
  .holder-name { font-weight: 900; font-size: 25px; color: var(--gold); letter-spacing: .5px; text-transform: uppercase; }
  .holder-title { font-size: 14px; color: var(--silver); margin-top: 2px; }
  .contacts { position: absolute; left: 282px; top: 96px; list-style: none; }
  .contacts li {
    display: flex; align-items: center; gap: 9px;
    font-size: 13px; color: var(--silver); line-height: 19px; white-space: nowrap;
  }
  .contacts svg { width: 11px; height: 11px; fill: var(--gold); flex: none; }
  .rule {
    position: absolute; left: 20px; right: 20px; bottom: 36px;
    height: 1px; background: var(--gold-line);
  }
  .address {
    position: absolute; left: 50%; bottom: 28px; transform: translateX(-50%);
    background: var(--card-back); padding: 0 10px;
    display: flex; align-items: center; gap: 6px;
    font-size: 12px; color: var(--silver); white-space: nowrap;
  }
  .address svg { width: 10px; height: 13px; fill: var(--gold); }
</style>
</head>
<body>
<main class="stage">
  <section class="card card-front" aria-label="Card front">
    <div class="brand">
      <span class="brand-mark"></span>
      <div class="brand-name">Renwick Tolliver<br>Construction</div>
    </div>
  </section>

  <section class="card card-back" aria-label="Card back">
    <div class="back-brand"><span class="brand-mark"></span>Renwick Tolliver Construction</div>

    <div class="holder">
      <div class="holder-name">Lionel Ashby</div>
      <div class="holder-title">Managing Director</div>
    </div>

    <ul class="contacts">
      <li><svg viewBox="0 0 24 24"><path d="M6.6 10.8a15 15 0 0 0 6.6 6.6l2.2-2.2c.3-.3.7-.4 1-.2 1.1.4 2.3.6 3.6.6.6 0 1 .4 1 1V20c0 .6-.4 1-1 1A17 17 0 0 1 3 4c0-.6.4-1 1-1h3.5c.6 0 1 .4 1 1 0 1.3.2 2.5.6 3.6.1.3 0 .7-.2 1z"/></svg>07822254961</li>
      <li><svg viewBox="0 0 24 24"><path d="M7 1h10a2 2 0 0 1 2 2v18a2 2 0 0 1-2 2H7a2 2 0 0 1-2-2V3a2 2 0 0 1 2-2zm0 3v14h10V4z"/></svg>07822254962</li>
      <li><svg viewBox="0 0 24 24"><path d="M6 2h12v6H6zM4 9h16a2 2 0 0 1 2 2v7h-4v4H6v-4H2v-7a2 2 0 0 1 2-2zm4 8v3h8v-3z"/></svg>07822254963</li>
      <li><svg viewBox="0 0 24 24"><path d="M2 5h20v14H2zm2 2v.5l8 5 8-5V7z"/></svg>info@renwick-tolliver</li>
      <li><svg viewBox="0 0 24 24"><circle cx="12" cy="12" r="10"/></svg>www.renwick-tolliver.co.uk</li>
    </ul>

    <div class="rule"></div>
    <div class="address">
      <svg viewBox="0 0 20 26"><path d="M10 0a10 10 0 0 0-10 10c0 7.5 10 16 10 16s10-8.5 10-16A10 10 0 0 0 10 0zm0 14a4 4 0 1 1 0-8 4 4 0 0 1 0 8z"/></svg>
      Your Address, City, State, Zip 1235
    </div>
  </section>
</main>
</body>
</html>
```